Harborline Renewal Business Card Design

Professional and clean design. The design colors should flow with the logo. Two-sided card with the website on the back which is:

www.HarborlineRenewal.example.

"Specializing in Water Damage Restoration"

On the front I need the name, email, phone, and logo.

Name: Darnell Quisby
Email: Darnell@HarborlineRenewal.example
Phone: 555-318-2046 for now

I only have the Preview and Thumbnail right now but should have the source files uploaded within a day or two.

Target Market(s)

Flood victims, home owners with water damage from busted pipes etc...

Industry/Entity Type

Business

Contact Information for Business Card

Name: Darnell Quisby

Font styles to use
Serif
Sans Serif

Requirements
Must have
• Business Card Details Info

```html
<!DOCTYPE html>
<html lang="en">
<head>
<meta charset="utf-8">
<title>Harborline Renewal Business Card</title>
<link rel="stylesheet" href="https://fonts.googleapis.com/css2?family=PT+Sans:wght@400;700&display=swap">
<style>
  :root {
    --page-bg: #e4e6e8;
    --card-white: #ffffff;
    --brand-blue: #2e9ad8;
    --brand-blue-deep: #1f7fc0;
    --swoosh-grey: #b9bcc0;
    --text-grey: #55585c;
    --text-white: #ffffff;
    --card-shadow: rgba(0, 0, 0, 0.18);
  }
  * { margin: 0; padding: 0; box-sizing: border-box; }
  html, body { width: 1200px; height: 843px; overflow: hidden; }
  body {
    background: var(--page-bg);
    font-family: "PT Sans", Arial, sans-serif;
    position: relative;
  }
  .card {
    position: absolute;
    top: 272px;
    width: 520px;
    height: 300px;
    border-radius: 22px;
    background: var(--card-white);
    box-shadow: 0 10px 28px var(--card-shadow);
    overflow: hidden;
  }
  .card-back { left: 50px; }
  .card-front { left: 630px; }

  /* Back */
  .back-mark {
    position: absolute;
    left: 50%;
    top: 58px;
    transform: translateX(-50%);
    width: 90px;
    height: 90px;
    border-radius: 50%;
    background: var(--brand-blue);
  }
  .back-name {
    position: absolute;
    top: 166px;
    width: 100%;
    text-align: center;
    font-weight: 700;
    font-size: 22px;
    color: var(--brand-blue-deep);
  }
  .back-tagline {
    position: absolute;
    bottom: 32px;
    width: 100%;
    text-align: center;
    font-weight: 700;
    font-size: 15px;
    color: var(--text-grey);
  }

  /* Front */
  .front-art { position: absolute; inset: 0; }
  .front-logo {
    position: absolute;
    right: 14px;
    top: 72px;
    width: 168px;
    text-align: center;
  }
  .logo-dot {
    display: block;
    width: 40px;
    height: 40px;
    margin: 0 auto 10px;
    border-radius: 50%;
    background: var(--brand-blue);
  }
  .logo-name {
    font-weight: 700;
    font-size: 18px;
    color: var(--brand-blue-deep);
    white-space: nowrap;
  }
  .contact {
    position: absolute;
    left: 24px;
    top: 112px;
    color: var(--text-white);
  }
  .contact-name {
    font-weight: 700;
    font-size: 21px;
    margin-bottom: 12px;
  }
  .contact-line {
    display: flex;
    align-items: center;
    gap: 8px;
    font-size: 13.5px;
    line-height: 21px;
    white-space: nowrap;
  }
  .contact-line svg { width: 12px; height: 12px; flex: none; }
</style>
</head>
<body>

  <section class="card card-back" aria-label="Card back">
    <div class="back-mark"></div>
    <div class="back-name">Harborline Renewal</div>
    <p class="back-tagline">Specializing in Water Damage Restoration</p>
  </section>

  <section class="card card-front" aria-label="Card front">
    <svg class="front-art" viewBox="0 0 520 300" preserveAspectRatio="none" aria-hidden="true">
      <defs>
        <linearGradient id="panelBlue" x1="0" y1="0" x2="1" y2="1">
          <stop offset="0" stop-color="#5cb6e8"/>
          <stop offset="1" stop-color="#1f7fc0"/>
        </linearGradient>
      </defs>
      <path d="M300,0 H336 C318,120 360,235 470,300 H430 C330,240 282,120 300,0 Z" fill="var(--swoosh-grey)"/>
      <path d="M0,0 H290 C272,120 320,240 420,300 H0 Z" fill="url(#panelBlue)"/>
    </svg>

    <div class="front-logo">
      <span class="logo-dot"></span>
      <div class="logo-name">Harborline Renewal</div>
    </div>

    <div class="contact">
      <div class="contact-name">Darnell Quisby</div>
      <div class="contact-line">
        <svg viewBox="0 0 12 12" aria-hidden="true"><path d="M2.5 1 L4.5 1 L5 3.5 L3.8 4.5 C4.5 6 6 7.5 7.5 8.2 L8.5 7 L11 7.5 L11 9.5 C11 10.5 10 11 9 11 C4.5 10.5 1.5 7.5 1 3 C1 2 1.5 1 2.5 1 Z" fill="#fff"/></svg>
        <span>555-318-2046 for now</span>
      </div>
      <div class="contact-line">
        <svg viewBox="0 0 12 12" aria-hidden="true"><rect x="0.5" y="2" width="11" height="8" rx="1" fill="#fff"/><path d="M1 2.5 L6 6.5 L11 2.5" fill="none" stroke="#2e9ad8" stroke-width="1"/></svg>
        <span>Darnell@HarborlineRenewal.example</span>
      </div>
      <div class="contact-line">
        <svg viewBox="0 0 12 12" aria-hidden="true"><circle cx="6" cy="6" r="5.5" fill="#fff"/><path d="M0.5 6 H11.5 M6 0.5 C3.5 3 3.5 9 6 11.5 M6 0.5 C8.5 3 8.5 9 6 11.5" fill="none" stroke="#2e9ad8" stroke-width="0.8"/></svg>
        <span>www.HarborlineRenewal.example</span>
      </div>
    </div>
  </section>

</body>
</html>
```